Advanced Therapeutic Massage Therapist

I need a business card advertising my massage services as an advanced therapeutic massage therapist. I offer advanced therapeutic massage, swedish and deep tissue. I want to create a simple, professional and feminine card. I like bright colours and creativity.

I prefer a bold and experimental approach rather than something status-quo. A card to suggest therapeutic healing through dynamic massage. Motifs, shapes or layout which suggest movement and flow.
Updates

Target Market(s)

Everybody!

Industry/Entity Type

Health And Wellness

Contact Information for Business Card

The card should include:
My name, logo, services offered and my contact details.

Sláine Dunleavy
Massage Therapist

- Swedish - Deep Tissue - Advanced Therapeutic

Phone: (+353) 87 216 4093
Email: regenerate@slainedunleavy-example.com
Website: www.slainedunlevy-example.com

Font styles to use
Serif
Sans Serif
Decorative
Script

Colors

Designer to choose colors to be used in the design.

Requirements
Must have
• An example may contain something like this, yet concise:
• "Sláine Dunleavy
• Massage Therapist
• - Swedish - Deep Tissue - Advanced Therapeutic"
Nice to have
• This sentence is optional:
• Imagery such as a logo or symbol. I have attached a file containing a logo I had produced however the name is incorrect now as it is "Sláine" not "Nelly". It could be edited to change it to Sláine.
• I have sent the file as .psd .jpg. .pdf and .png
• I like when the card conveys energy, movement, pressure points, flow etc.
• I just like the designer to follow their own style and ideas. I like bright colours but must have a lot of a base colour to offset it. I really prefer them to follow their own inspiration. That is my preference.
Should not have
• Pine trees, non-native trees to Britain and Ireland, exotic flowers or animals that are not native to Britain and Ireland.
• I don't like brown as the background colour of the card.
• The cars shouldn't look like a wedding invitation i.e too many floral type designs.

```html
<!DOCTYPE html>
<html lang="en">
<head>
<meta charset="utf-8">
<title>Sláine Dunleavy – Massage Therapist Business Card</title>
<link href="https://fonts.googleapis.com/css2?family=Great+Vibes&family=Quicksand:wght@400;500&family=Overpass:wght@600&display=swap" rel="stylesheet">
<style>
  :root {
    --stage: #666666;
    --card-dark: #222222;
    --card-edge: #2c2c2c;
    --aqua-deep: #8fd1c1;
    --mint-text: #6cc4a4;
    --ink: #1f1f1f;
    --white: #ffffff;
  }
  html, body {
    margin: 0;
    padding: 0;
    width: 1200px;
    height: 550px;
    overflow: hidden;
    background: var(--stage);
  }
  .stage {
    position: relative;
    width: 1200px;
    height: 550px;
  }
  .card {
    position: absolute;
    top: 157px;
    width: 390px;
    height: 235px;
    background: radial-gradient(circle at 50% 40%, var(--card-edge), var(--card-dark) 75%);
    overflow: hidden;
  }
  .card--front { left: 195px; }
  .card--back { left: 613px; }

  .emblem {
    position: absolute;
    border-radius: 50%;
    background: var(--aqua-deep);
  }
  .card--front .emblem { left: 138px; top: 32px; width: 114px; height: 114px; }
  .card--back .emblem { left: 26px; top: 55px; width: 134px; height: 134px; }

  .name-block {
    position: absolute;
    text-align: center;
    color: var(--white);
  }
  .name {
    font-family: "Great Vibes", cursive;
    font-size: 25px;
    line-height: 1;
    margin: 0;
  }
  .role {
    font-family: "Quicksand", sans-serif;
    font-size: 9.5px;
    letter-spacing: 0.8px;
    margin: 1px 0 0;
  }
  .card--front .name-block { left: 0; right: 0; top: 150px; }
  .card--back .name-block { left: 200px; width: 180px; top: 138px; }
  .card--back .name { font-size: 26px; }

  .tagline {
    position: absolute;
    left: 0;
    right: 0;
    top: 211px;
    text-align: center;
    font-family: "Overpass", sans-serif;
    font-weight: 600;
    font-size: 9px;
    color: var(--mint-text);
    margin: 0;
  }

  .waves {
    position: absolute;
    left: 0;
    top: 0;
  }

  .contact {
    position: absolute;
    right: 15px;
    top: 14px;
    margin: 0;
    padding: 0;
    list-style: none;
    text-align: right;
    font-family: "Quicksand", sans-serif;
    font-weight: 500;
    font-size: 10.5px;
    line-height: 17px;
    color: var(--ink);
  }

  .services {
    position: absolute;
    left: 0;
    right: 0;
    top: 211px;
    display: flex;
    align-items: center;
    justify-content: center;
    gap: 10px;
    font-family: "Quicksand", sans-serif;
    font-size: 10.5px;
    color: var(--mint-text);
    margin: 0;
  }
  .services::before,
  .services::after {
    content: "";
    width: 38px;
    height: 1.5px;
    background: linear-gradient(90deg, transparent, var(--white));
  }
  .services::after {
    background: linear-gradient(90deg, var(--white), transparent);
  }
</style>
</head>
<body>
<main class="stage">

  <section class="card card--front" aria-label="Business card front">
    <div class="emblem" role="img" aria-label="Round brand emblem area"></div>
    <div class="name-block">
      <p class="name">Sláine Dunleavy</p>
      <p class="role">massage therapist</p>
    </div>
    <p class="tagline">IHTB qualified, specializing in Advanced Therapeutic &amp; Deep Tissue Massage</p>
  </section>

  <section class="card card--back" aria-label="Business card back">
    <svg class="waves" width="390" height="235" viewBox="0 0 390 235" aria-hidden="true">
      <defs>
        <linearGradient id="aquaWash" x1="0" y1="0" x2="1" y2="1">
          <stop offset="0" stop-color="#a9ddd0"/>
          <stop offset="0.6" stop-color="#c6ebe2"/>
          <stop offset="1" stop-color="#9fd8c9"/>
        </linearGradient>
        <linearGradient id="goldSheen" x1="0" y1="0" x2="1" y2="0">
          <stop offset="0" stop-color="#c8952a"/>
          <stop offset="0.5" stop-color="#f7d35a"/>
          <stop offset="1" stop-color="#f2c94c"/>
        </linearGradient>
      </defs>
      <path d="M0 0 H390 V112 C300 100 200 20 0 8 Z" fill="url(#aquaWash)"/>
      <path d="M0 12 C150 14 230 60 300 88 C335 100 365 106 390 108 V118 C330 116 280 98 220 72 C150 40 80 30 0 40 Z" fill="#1b1b1b"/>
      <path d="M0 30 C90 8 170 30 215 46 C150 28 80 30 0 44 Z" fill="url(#goldSheen)"/>
      <path d="M14 46 C120 30 210 66 280 96 C320 112 360 118 390 116 V124 C350 126 310 118 270 104 C200 78 120 46 14 46 Z" fill="url(#goldSheen)"/>
    </svg>

    <ul class="contact">
      <li>regenerate@slainedunleavy-example.com</li>
      <li>www.slainedunlevy-example.com</li>
      <li>(+353) 87 216 4093</li>
    </ul>

    <div class="emblem" role="img" aria-label="Round brand emblem area"></div>

    <div class="name-block">
      <p class="name">Sláine Dunleavy</p>
      <p class="role">massage therapist</p>
    </div>

    <p class="services">Swedish - Deep Tissue - Advanced Therapeutic</p>
  </section>

</main>
</body>
</html>
```